4D Cradle Glimpse Luxury Ultrasound Billboard

Design a HIGH-END, MODERN billboard for my private prenatal ultrasound studio, 4D Cradle Glimpse, located in Pace, Florida.
This billboard will be viewed by drivers traveling at highway speeds, so it must be extremely clean, simple, and readable within 6 seconds.
About My Business
4D Cradle Glimpse is a private prenatal ultrasound studio specializing in:
Highest technology 4D/HD Ultrasounds
Early Gender Determination
Pregnancy Confirmation
I have been serving families for nearly 10 years and is known for creating a memorable experience, not just an ultrasound appointment.
Design Style
I DO NOT want:
Flowers
Leaves
Swirls
Glitter
Hearts everywhere
Busy backgrounds
Generic maternity stock graphics
I DO want:
Modern
Luxury
Upscale
Clean
Professional
Eye-catching
Premium medical spa feel
Colors
Use colors from my logo:
LOGO Green ( or a deep green)
Black
White
Soft Gold accents
Images:
Incorporate my professional headshot in a clean, modern way, logo, and the ultrasound images
Text
Keep wording minimal.
Primary Headline ( OPEN TO IDEAS) :
EXAMPLES ( WOULD RATHER SOMETHING MORE CATCHY)
" ADVANCED IMAGING. UNFORGETTABLE MOMENTS"
"MEET YOUR BABY BEFORE BIRTH"
Under headline:
4D Ultrasound • Early Gender • Pregnancy Confirmation
Business Name:
4D Cradle Glimpse
Private Prenatal Ultrasound Studio
Phone Number:
850-471-5923
Important
This billboard must be readable in 5–6 seconds from a moving vehicle.
Less text is better.
The phone number and business name must be visible from a distance.
The design should feel like a premium brand that immediately tells expecting parents:
“This is where I go to see my baby.”
Files Provided
Official logo
Headshot
Ultrasound images
Don’t make this look like a medical office billboard.
Make it look like a luxury baby experience billboard. That’s what separates 4D Cradle Glimpse from hospitals, OB offices, and all the new studios popping up around you. The emotional connection is what gets moms to book. ❤️
Billboard Size - 10.6” x 36”

```html
<!DOCTYPE html>
<html lang="en">
<head>
<meta charset="utf-8">
<title>4D Cradle Glimpse Billboard</title>
<link rel="stylesheet" href="https://fonts.googleapis.com/css2?family=Playfair+Display:wght@700;800&family=Playball&family=Great+Vibes&family=Montserrat:wght@600;800&display=swap">
<style>
  :root {
    --deep-green: #0f2a1c;
    --band-green: #143524;
    --gold: #c9a018;
    --gold-light: #e8c66a;
    --gold-dark: #a9741d;
    --cream: #f8f2e7;
    --white: #ffffff;
    --stage: #d4d4d4;
  }
  * { margin: 0; padding: 0; box-sizing: border-box; }
  html, body {
    width: 1200px; height: 422px; overflow: hidden;
    background: var(--stage);
  }
  .billboard {
    position: absolute; left: 49px; top: 63px;
    width: 1100px; height: 310px; overflow: hidden;
    background: radial-gradient(ellipse at 55% 40%, var(--white) 0%, var(--cream) 70%, #efe4d0 100%);
  }
  .billboard-shapes { position: absolute; inset: 0; }

  .logo-box {
    position: absolute; left: 14px; top: 11px; width: 240px; height: 108px;
    border: 3px solid var(--deep-green); border-radius: 12px;
    background: rgba(255,255,255,0.9);
    display: flex; flex-direction: column; align-items: center; justify-content: center;
    z-index: 2;
  }
  .logo-name {
    font-family: "Playfair Display", serif; font-weight: 700;
    color: var(--deep-green); font-size: 24px; line-height: 1.05; text-align: center;
  }
  .logo-tagline {
    margin-top: 10px;
    font-family: "Montserrat", sans-serif; font-weight: 600;
    font-size: 9.5px; letter-spacing: 0.2px; color: var(--deep-green);
  }

  .care-line {
    position: absolute; left: 33px; top: 142px;
    font-family: "Great Vibes", cursive; font-size: 22px; line-height: 1.05;
    color: var(--deep-green); transform: rotate(-10deg); transform-origin: left top;
  }
  .care-line span { display: block; padding-left: 14px; }

  .headshot {
    position: absolute; left: 258px; top: 50px; width: 136px; height: 260px;
    border-radius: 68px 68px 0 0;
    background: linear-gradient(180deg, #e9c88a 0%, #d9a878 35%, #1f4a33 60%, #173a28 100%);
  }

  .headline {
    position: absolute; left: 361px; top: 0; width: 440px; height: 170px;
    color: var(--deep-green); font-family: "Playfair Display", serif; font-weight: 800;
  }
  .headline-top { position: absolute; left: 0; top: 8px; font-size: 52px; letter-spacing: 3px; line-height: 1; white-space: nowrap; }
  .headline-script {
    position: absolute; left: 99px; top: 26px;
    font-family: "Playball", cursive; font-weight: 400; font-size: 108px; line-height: 1;
    background: linear-gradient(180deg, var(--gold-light), var(--gold-dark));
    -webkit-background-clip: text; background-clip: text; color: transparent;
  }
  .headline-bottom { position: absolute; left: 60px; top: 122px; font-size: 44px; letter-spacing: 2px; line-height: 1; white-space: nowrap; }

  .services {
    position: absolute; left: 405px; top: 182px; width: 420px; text-align: center;
    font-family: "Montserrat", sans-serif; font-weight: 800; font-size: 22px;
    color: var(--gold); line-height: 28px; letter-spacing: 0.6px;
  }

  .phone-pill {
    position: absolute; left: 396px; top: 263px; width: 482px; height: 47px;
    border-radius: 24px 24px 0 0; border: 3px solid var(--gold); border-bottom: none;
    background: linear-gradient(180deg, #1d4630, var(--deep-green));
    display: flex; align-items: center; padding: 2px 0 0 20px; gap: 12px;
  }
  .phone-icon { width: 36px; height: 36px; flex: none; }
  .phone-number {
    font-family: "Montserrat", sans-serif; font-weight: 800;
    font-size: 38px; line-height: 40px; color: var(--white); letter-spacing: 0.5px;
  }
</style>
</head>
<body>
  <main class="billboard">
    <svg class="billboard-shapes" viewBox="0 0 1100 310" width="1100" height="310" aria-hidden="true">
      <defs>
        <linearGradient id="goldStroke" x1="0" y1="0" x2="1" y2="0">
          <stop offset="0" stop-color="#a9741d"/>
          <stop offset="0.5" stop-color="#f0d68a"/>
          <stop offset="1" stop-color="#a9741d"/>
        </linearGradient>
        <radialGradient id="scanGlow" cx="0.55" cy="0.45" r="0.7">
          <stop offset="0" stop-color="#f0a060"/>
          <stop offset="0.55" stop-color="#d9772f"/>
          <stop offset="1" stop-color="#5a2208"/>
        </radialGradient>
      </defs>
      <path class="lower-band" d="M0 200 C60 230 140 250 220 258 L1100 262 L1100 310 L0 310 Z" fill="#143524"/>
      <path class="lower-band-edge" d="M0 200 C60 230 140 250 220 258 L1100 262" fill="none" stroke="url(#goldStroke)" stroke-width="4"/>
      <path class="headline-rule" d="M421 168 C540 160 680 160 785 166" fill="none" stroke="url(#goldStroke)" stroke-width="2"/>
      <g class="scan-heart" role="img" aria-label="Warm-toned 4D ultrasound image of twin babies inside a heart frame">
        <path d="M915 292 C860 230 800 150 805 90 C810 35 860 5 905 8 C945 10 975 30 985 55 C1000 20 1040 0 1090 0 L1100 0 L1100 262 C1040 270 960 280 915 292 Z" fill="url(#scanGlow)"/>
        <path d="M915 292 C860 230 800 150 805 90 C810 35 860 5 905 8 C945 10 975 30 985 55 C1000 20 1040 0 1090 0 L1100 0" fill="none" stroke="url(#goldStroke)" stroke-width="5"/>
      </g>
    </svg>

    <div class="logo-box">
      <div class="logo-name">4D<br>Cradle Glimpse</div>
      <div class="logo-tagline">PRENATAL ULTRASOUND STUDIO</div>
    </div>

    <p class="care-line">Compassionate Care,<span>Precious Memories</span></p>

    <div class="headshot" role="img" aria-label="Professional headshot of the studio owner in green scrubs holding an ultrasound probe"></div>

    <h1 class="headline">
      <span class="headline-top">MEET YOUR</span>
      <span class="headline-script">Baby</span>
      <span class="headline-bottom">BEFORE BIRTH</span>
    </h1>

    <p class="services">4D Ultrasound • Early Gender<br>• Pregnancy Confirmation</p>

    <div class="phone-pill">
      <svg class="phone-icon" viewBox="0 0 44 44" aria-hidden="true">
        <circle cx="22" cy="22" r="21" fill="#c98a25" stroke="#f0d68a" stroke-width="2"/>
        <path d="M15 11 C13 12 11 14 12 18 C14 26 19 31 27 33 C30 34 32 32 33 30 L29 26 L26 28 C22 26 19 23 17 19 L19 16 Z" fill="#ffffff"/>
      </svg>
      <span class="phone-number">850-471-5923</span>
    </div>
  </main>
</body>
</html>
```